Larkhollow needs a Webpage Design

We need a webpage for Dr. XYZ who is doing consultancy practice in the area of speech, language, and reading disabilities. He is doing his consultancy practice as "Larkhollow Consultants". Our target market is clients with annual income of $100,000 or more in Chicago area. Our business philosophy is: "...We provide the best evidence-based services/interventions, at an affordable fee, and deal only with clients who seek such services...."

Dr. XYZ's area of research interests are: a) using assistive technology for communication for children with autism, b) early intervention with focus on parent participation, and c) language learning for children birth-to-five years.

He works at a public university whose school color is 'Orange". Home page should show two logos (university and practice). Each page should stand on its own and reflect the content with minimal scrolling. The colors should be subdued (not bright colors) to attract college educated wealthy individuals who are seeking best evidence-based practice in speech, language, and reading for their children.

We need five pages: Home, Consultation, Research, Professional Development, and Contact (with google map directions). The home page should have space for a picture and links for facebook, twitter, and google plus. Other pages should have space for at least one picture and links to pdf files.

The overall design should show healthcare service, evidence-based early intervention with focus on parent participation, and project that we are leaders in the field.

```html
<!DOCTYPE html>
<html lang="en">
<head>
<meta charset="utf-8">
<title>Larkhollow Consultants</title>
<link href="https://fonts.googleapis.com/css2?family=Open+Sans:wght@400;600;700&family=Libre+Baskerville&display=swap" rel="stylesheet">
<style>
:root{
  --brand:#1f6fb6;
  --brand-dark:#16558f;
  --navy:#0f3a6a;
  --navy-2:#1b5d9c;
  --ink:#4a4a4a;
  --muted:#8a8a8a;
  --line:#d9dde2;
  --btn-grey:#8d9296;
  --white:#fff;
}
*{box-sizing:border-box;margin:0;padding:0}
html,body{width:849px;height:1200px;overflow:hidden;background:#fff}
body{position:relative;font-family:"Open Sans",Arial,sans-serif;color:var(--ink)}
.abs{position:absolute}

/* header */
.topbar{left:0;top:0;width:849px;height:40px;background:linear-gradient(#2479c2,var(--brand))}
.brand{left:22px;top:7px;color:var(--white);font-size:21px;font-weight:400;letter-spacing:.2px}
.utility{right:20px;top:13px;display:flex;align-items:center;gap:12px;color:var(--white);font-size:8px}
.utility .search{width:62px;height:14px;background:var(--white);border-radius:2px}
.nav{left:0;top:40px;width:849px;height:24px;background:#fff;border-bottom:1px solid var(--line)}
.nav a{position:absolute;top:6px;font-size:9.5px;color:#2b5d94;text-decoration:none}
.nav a.active{font-weight:600}
.nav a.active::after{content:"";position:absolute;left:-14px;right:-14px;bottom:-7px;height:3px;background:var(--brand)}

/* hero */
.hero{left:0;top:64px;width:849px;height:383px;background:linear-gradient(100deg,#c9d3c4 0%,#a7b8a0 30%,#e6dcc6 55%,#f4efe6 75%,#b9c7b6 100%)}
.hero-copy{left:24px;top:258px;width:330px;color:var(--white)}
.hero-title{font-family:"Libre Baskerville",Georgia,serif;font-size:24px;font-weight:400;white-space:nowrap}
.hero-lead{margin-top:6px;font-size:11.5px;line-height:1.3}
.hero-small{font-size:7px;line-height:1.3;margin-top:2px;opacity:.9}
.hero-actions{margin-top:10px;display:flex;gap:8px}
.btn{display:inline-block;font-size:8px;color:var(--white);padding:4px 10px;border-radius:2px}
.btn-blue{background:var(--brand)}
.btn-dark{background:#2f3336}
.btn-grey{background:var(--btn-grey)}
.arrow{top:290px}

/* research */
.section-title{color:var(--brand);font-size:18px;font-weight:600}
.research-title{left:0;width:849px;top:490px;text-align:center}
.card{top:523px;width:210px;text-align:center}
.card .thumb{height:122px;border:1px solid var(--line);background:linear-gradient(135deg,#e9eef2,#cfd9e2)}
.card p{margin:8px auto 0;width:170px;font-size:8.5px;line-height:1.35;color:var(--ink)}
.card p.lead{font-weight:600}
.card .btn{margin-top:8px;font-size:7px;padding:3px 10px}
.rule{left:70px;top:742px;width:710px;height:1px;background:var(--line)}

/* about */
.about-title{left:70px;top:756px;font-size:15px}
.about-photo{left:70px;top:786px;width:132px;height:120px;border:1px solid var(--line);background:linear-gradient(135deg,#dfe5ea,#b8c4cf)}
.about-text{left:214px;top:788px;width:230px;font-size:7.5px;line-height:1.45;color:var(--muted)}
.consult{left:624px;top:780px;width:156px;height:138px;background:linear-gradient(var(--brand),var(--brand-dark));color:var(--white);padding:12px 12px;text-align:center}
.consult h3{font-size:14px;font-weight:400;padding-bottom:6px;border-bottom:1px solid rgba(255,255,255,.35)}
.consult p{margin-top:8px;font-size:7px;line-height:1.45;text-align:left;opacity:.9}
.consult .btn{margin-top:9px;background:var(--navy);font-size:7px}

/* footer */
.footer{left:0;top:963px;width:849px;height:237px;background:linear-gradient(160deg,var(--navy) 0%,var(--navy-2) 60%,#2c79bd 100%);color:var(--white)}
.footer h4{font-size:13px;font-weight:600}
.col{top:20px}
.contact-row{display:flex;gap:7px;margin-top:10px;font-size:7.5px;line-height:1.4;opacity:.85}
.col p{font-size:7.5px;line-height:1.45;opacity:.85;margin-top:8px}
.pill{margin-top:9px;width:170px;height:18px;border-radius:9px;background:rgba(255,255,255,.12);display:flex;align-items:center;gap:8px;padding-left:4px;font-size:7.5px}
.pill i{width:11px;height:11px;border-radius:50%;background:var(--brand);display:block}
.field{background:rgba(255,255,255,.9);height:15px;border-radius:2px;font-size:7px;color:var(--muted);padding:3px 5px}
.form-row{display:flex;gap:8px;margin-top:10px}
.form-row .field{width:95px}
.message{margin-top:8px;width:198px;height:50px}
.send{margin-top:8px;margin-left:148px;width:50px;text-align:center;background:var(--white);color:var(--navy);font-size:7.5px;padding:3px 0;border-radius:2px}
.footer-rule{left:70px;top:200px;width:710px;height:1px;background:rgba(255,255,255,.25)}
.copyright{left:70px;top:212px;font-size:7px;opacity:.75}
.social{right:70px;top:208px;display:flex;gap:6px}
.social span{width:14px;height:14px;border-radius:50%;background:rgba(255,255,255,.85);display:block}
</style>
</head>
<body>

<header class="abs topbar">
  <div class="abs brand">Larkhollow Consultants.</div>
  <div class="abs utility">
    <span style="display:flex;align-items:center;gap:4px">
      <svg width="8" height="9" viewBox="0 0 8 9"><path d="M1 .5h2l1 2-1.2 1a5 5 0 0 0 2.2 2.2L6 4.5l2 1v2c0 .6-.5 1-1 1A7 7 0 0 1 0 1.5c0-.6.4-1 1-1z" fill="#fff"/></svg>
      +1 312 555 0148
    </span>
    <span>Sign up</span>
    <span>Login</span>
    <span class="search"></span>
  </div>
</header>

<nav class="abs nav">
  <a class="active" style="left:30px">Home</a>
  <a style="left:138px">Consultation</a>
  <a style="left:290px">Research</a>
  <a style="left:415px">Professional Development</a>
  <a style="left:618px">Contact</a>
</nav>

<section class="abs hero" role="img" aria-label="Photo of a woman with glasses smiling while reading a book">
</section>
<svg class="abs arrow" style="left:8px" width="12" height="20" viewBox="0 0 12 20"><path d="M10 2 2 10l8 8" fill="none" stroke="#fff" stroke-width="2"/></svg>
<svg class="abs arrow" style="right:8px" width="12" height="20" viewBox="0 0 12 20"><path d="M2 2l8 8-8 8" fill="none" stroke="#fff" stroke-width="2"/></svg>
<div class="abs hero-copy">
  <h1 class="hero-title">Larkhollow Consultant</h1>
  <p class="hero-lead">consultancy practice in the area of speech, language, and Reading disabilities.</p>
  <p class="hero-small">Evidence-based care for children and families, built on research and guided by trust.</p>
  <div class="hero-actions">
    <span class="btn btn-blue">View our Projects</span>
    <span class="btn btn-dark">Read More</span>
  </div>
</div>

<h2 class="abs section-title research-title">Our research</h2>

<article class="abs card" style="left:78px">
  <div class="thumb" role="img" aria-label="Child using a tablet for communication"></div>
  <p class="lead">Using assistive technology for Communication for children with autism</p>
  <span class="btn btn-blue">Read More</span>
</article>
<article class="abs card" style="left:320px">
  <div class="thumb" role="img" aria-label="Illustration of parent participation with a child"></div>
  <p>Early intervention with focus on parent participation</p>
  <span class="btn btn-grey">Read More</span>
</article>
<article class="abs card" style="left:562px">
  <div class="thumb" role="img" aria-label="Young child playing and learning language"></div>
  <p>Language learning for children birth-to-five years.</p>
  <span class="btn btn-grey">Read More</span>
</article>

<div class="abs rule"></div>

<h2 class="abs section-title about-title">About Us</h2>
<div class="abs about-photo" role="img" aria-label="Group photo of the consultancy team"></div>
<p class="abs about-text">Established with a clear purpose, our practice offers careful assessment and therapy for speech, language and reading needs. Each plan is shaped by current research and the goals of the family. We work closely with parents so that progress carries on at home, at school and in daily life. Our team brings years of clinical and university experience to every session, and we measure results so families can see real growth over time.</p>

<aside class="abs consult">
  <h3>Consultation</h3>
  <p>Book a one-to-one session to discuss your child's needs. We review history, assess skills and agree a clear plan with you before therapy begins.</p>
  <span class="btn">Consult Now</span>
</aside>

<footer class="abs footer">
  <div class="abs col" style="left:70px;width:200px">
    <h4>Contacts</h4>
    <div class="contact-row">
      <svg width="8" height="11" viewBox="0 0 8 11"><path d="M4 0a4 4 0 0 1 4 4c0 3-4 7-4 7S0 7 0 4a4 4 0 0 1 4-4z" fill="#fff"/><circle cx="4" cy="4" r="1.5" fill="#1b5d9c"/></svg>
      <span>LARKHOLLOW CONSULTANTS<br>2140 Wren Hollow Ave<br>Suite 4<br>Chicago IL 60614</span>
    </div>
    <div class="contact-row">
      <svg width="9" height="9" viewBox="0 0 8 9"><path d="M1 .5h2l1 2-1.2 1a5 5 0 0 0 2.2 2.2L6 4.5l2 1v2c0 .6-.5 1-1 1A7 7 0 0 1 0 1.5c0-.6.4-1 1-1z" fill="#fff"/></svg>
      <span>+1 312 555 0148</span>
    </div>
    <div class="contact-row">
      <svg width="10" height="8" viewBox="0 0 10 8"><rect width="10" height="8" rx="1" fill="#fff"/><path d="M0 .5 5 4.5 10 .5" fill="none" stroke="#1b5d9c"/></svg>
      <span>hello@larkhollow.example</span>
    </div>
  </div>

  <div class="abs col" style="left:318px;width:200px">
    <h4>Carrier</h4>
    <p>We welcome skilled therapists who share our focus on evidence-based practice and family-centred care.</p>
    <div class="pill"><i></i>Join our team</div>
    <div class="pill"><i></i>Current openings</div>
  </div>

  <div class="abs col" style="left:582px;width:200px">
    <h4>Contact Us</h4>
    <div class="form-row"><div class="field">Name</div><div class="field">Email</div></div>
    <div class="field message">Message</div>
    <div class="send">Send now</div>
  </div>

  <div class="abs footer-rule"></div>
  <div class="abs copyright">Copyright 2014 Larkhollow Consultants. All rights reserved.</div>
  <div class="abs social"><span></span><span></span><span></span><span></span></div>
</footer>

</body>
</html>
```